Brimlow OrthoLink IT Inc. new website

i need a website for my company which is dedicated to installation and service of computer systems in Dental Offices. I would like for it to encompass a technology feel and professional look. The company deals with all aspects of technology like, Audio Visual, computer systems and networks, Cloud services like data backup, data center. We provide manage services, support and services to Dental Professionals.
Updates

Looking for a Technology font but professional look Added Wednesday, April 20, 2016

Target Market(s)

Dental, Dentist

Industry/Entity Type

Dental

Number of Pages Required

5+ page

Font styles to use
Other font styles liked:
• Futuristic or Techy

Colors
0255a3
ec1f27

Requirements
Must have
• Tabs
Nice to have
• Have no idea maybe some suggestion on your part may help
Should not have
• A professional feel but have a techy look

```html
<!DOCTYPE html>
<html lang="en">
<head>
<meta charset="utf-8">
<title>Brimlow OrthoLink IT Inc. — Support</title>
<link rel="stylesheet" href="https://fonts.googleapis.com/css2?family=Exo+2:wght@600;700;800&family=Lato:wght@400;700&family=Oswald:wght@400&display=swap">
<style>
:root{
  --brand-blue:#0255a3;
  --bar-blue:#0a82c4;
  --link-blue:#1a8fd6;
  --ink:#111;
  --body:#222;
  --footer:#2f2f2f;
  --footer-deep:#1f1f1f;
  --field:#1c1c1c;
  --rule:#c9c9c9;
}
*{margin:0;padding:0;box-sizing:border-box}
html,body{width:1017px;height:1200px;overflow:hidden;background:#fff}
body{position:relative;font-family:"Lato",sans-serif;color:var(--body)}
.abs{position:absolute}

.topbar{left:0;top:0;width:1017px;height:32px;background:var(--bar-blue)}
.topbar-phone{left:670px;top:5px;color:#fff;font-family:"Oswald",sans-serif;font-size:17px;letter-spacing:.5px;display:flex;align-items:center;gap:8px}
.topbar-sep{left:804px;top:6px;width:1px;height:20px;background:rgba(255,255,255,.35)}
.social{display:flex;gap:8px}
.social span{display:block;width:24px;height:24px;border:2px solid #fff;border-radius:3px;background:rgba(255,255,255,.2)}
.topbar-social{left:818px;top:4px}

.brand{left:112px;top:52px;display:flex;align-items:center;gap:10px}
.brand-mark{width:14px;height:14px;background:var(--brand-blue)}
.brand-name{font-family:"Exo 2",sans-serif;font-weight:800;color:var(--brand-blue);font-size:22px;line-height:24px}
.nav{left:393px;top:70px;display:flex;align-items:center;height:20px}
.nav a{font-family:"Exo 2",sans-serif;font-weight:700;font-size:14px;color:var(--ink);text-decoration:none;letter-spacing:.3px;padding:0 25px;border-left:1px solid #b8d4ea;line-height:18px}
.nav a:first-child{border-left:none;padding-left:0;padding-right:24px}
.nav a.active{color:var(--link-blue)}
.nav a:last-child{padding-right:0}

.hero{left:0;top:130px;width:1017px;height:254px;background:linear-gradient(90deg,#c3c8d0 0%,#8d97aa 18%,#34405a 42%,#1b2744 62%,#27426e 82%,#5d6f90 100%)}
.hero-line-top{left:264px;top:162px;font-family:"Exo 2",sans-serif;font-size:32px;font-weight:700;color:#fff;white-space:nowrap;text-shadow:0 1px 3px rgba(0,0,0,.4)}
.hero-frame{left:407px;top:210px;width:572px;height:97px;border:1px solid rgba(255,255,255,.55);background:rgba(20,40,80,.25)}
.hero-big{left:428px;top:220px;font-family:"Exo 2",sans-serif;font-weight:800;font-size:60px;color:#fff;letter-spacing:1px;line-height:76px}
.hero-rings{left:738px;top:222px}
.hero-line-bottom{left:430px;top:311px;font-family:"Exo 2",sans-serif;font-size:31px;font-weight:700;color:#fff;white-space:nowrap;text-shadow:0 1px 3px rgba(0,0,0,.4)}

.section-title{left:0;top:422px;width:1017px;text-align:center;font-family:"Exo 2",sans-serif;font-size:29px;font-weight:800;color:var(--ink)}
.divider{left:318px;top:480px;width:381px;height:1px;background:var(--rule)}
.divider-mark{left:501px;top:473px;width:16px;height:14px;border-radius:2px;background:#8d8d8d}
.lead{left:113px;top:502px;width:793px;font-size:13px;line-height:23px;letter-spacing:.2px}
.photo{left:112px;top:620px;width:278px;height:175px;background:linear-gradient(120deg,#7dbfa8 0%,#d9cfb7 40%,#b89c6e 65%,#5c5e63 100%)}
.side-text{left:415px;top:618px;width:491px;font-size:13px;line-height:23px;letter-spacing:.2px}

.footer{left:0;top:843px;width:1017px;height:314px;background:radial-gradient(ellipse at 50% 40%,#3a3a3a,var(--footer) 70%)}
.footer-title{position:absolute;font-family:"Exo 2",sans-serif;font-weight:700;font-size:17px;color:#fff}
.footer-underline{position:absolute;height:0;border-top:1px dotted #9a9a9a}
.footer-rule{position:absolute;top:925px;width:2px;height:180px;background:linear-gradient(#2f2f2f,#202020 50%,#2f2f2f)}
.quick{left:113px;top:922px;list-style:none}
.quick li{color:#fff;font-size:13px;height:36px;display:flex;gap:8px;align-items:center}
.quick li::before{content:"›";font-size:13px}
.quick li.current{font-weight:700}
.contact{left:288px;top:932px;color:#fff;font-size:13px}
.contact-row{position:absolute;left:0;display:flex;gap:14px;width:250px}
.contact-row svg{flex:none;margin-top:2px}
.contact-address{display:block;line-height:17px;margin-top:3px;font-size:12.5px;white-space:nowrap}
.form{left:530px;top:938px;width:207px}
.field{background:var(--field);color:#9a9a9a;font-size:12px;height:25px;padding:5px 10px;margin-bottom:4px}
.field-message{height:64px}
.submit{margin-top:8px;width:81px;height:28px;background:var(--brand-blue);color:#fff;font-weight:700;font-size:16px;text-align:center;line-height:28px;box-shadow:0 1px 3px rgba(0,0,0,.5)}
.foot-brand{left:790px;top:945px;width:126px;text-align:center;color:#8d8d8d;font-family:"Exo 2",sans-serif;font-weight:800;font-size:18px;line-height:22px}
.footer-social{left:808px;top:1062px}
.footer-social span{border-color:#ddd;background:#555}
.copy{left:0;top:1157px;width:1017px;height:43px;background:var(--footer-deep);color:#ddd;font-size:12px;text-align:center;line-height:43px}
</style>
</head>
<body>

<header>
  <div class="abs topbar"></div>
  <div class="abs topbar-phone">
    <svg width="20" height="20" viewBox="0 0 20 20"><circle cx="10" cy="10" r="9" fill="none" stroke="#fff" stroke-width="1.6"/><path d="M7 5.5l1.6 2.4-1 1.1c.6 1.4 1.6 2.4 3 3l1.1-1 2.4 1.6-.9 1.6c-3.4-.2-6.6-3.4-6.8-6.8z" fill="#fff"/></svg>
    555-014-2290
  </div>
  <div class="abs topbar-sep"></div>
  <div class="abs social topbar-social" aria-label="Social links"><span></span><span></span><span></span></div>

  <div class="abs brand">
    <span class="brand-mark"></span>
    <div class="brand-name">Brimlow OrthoLink<br>IT Inc.</div>
  </div>
  <nav class="abs nav">
    <a href="#" aria-label="Home"><svg width="24" height="20" viewBox="0 0 24 20"><path d="M12 1L1 10.5h3V19h6v-6h4v6h6v-8.5h3z" fill="#111"/></svg></a>
    <a href="#">ABOUT US</a>
    <a href="#">SERVICES</a>
    <a href="#" class="active">SUPPORT</a>
    <a href="#">CONTACT US</a>
  </nav>
</header>

<section>
  <div class="abs hero" role="img" aria-label="Dental treatment chair on the left blending into a business professional touching a screen on the right"></div>
  <div class="abs hero-line-top">We Provide Manage Services,</div>
  <div class="abs hero-frame"></div>
  <div class="abs hero-big">SUPPORT</div>
  <svg class="abs hero-rings" width="230" height="74" viewBox="0 0 230 74">
    <g fill="#6f87ad" stroke="#fff" stroke-width="4">
      <circle cx="37" cy="37" r="33"/><circle cx="115" cy="37" r="33"/><circle cx="193" cy="37" r="33"/>
    </g>
    <path d="M100 30h8l10-9v32l-10-9h-8z" fill="#fff"/>
    <path d="M124 28q5 9 0 18M129 23q9 14 0 28" fill="none" stroke="#fff" stroke-width="3"/>
    <g fill="#fff"><rect x="178" y="22" width="12" height="30"/><rect x="194" y="22" width="16" height="8"/><rect x="194" y="33" width="16" height="8"/><rect x="194" y="44" width="16" height="8"/></g>
  </svg>
  <div class="abs hero-line-bottom">&amp; Service To Dental Professionals.</div>
</section>

<main>
  <h1 class="abs section-title">Support</h1>
  <div class="abs divider"></div>
  <div class="abs divider-mark"></div>
  <p class="abs lead">Lorem ipsum dolor sit amet, consectetuer adipiscing elit, sed diam nonummy nibh euismod tincidunt ut laoreet dolore magna aliquam erat volutpat. Ut wisi enim ad minim veniam, quis nostrud exerci tation ullamcorper suscipit lobortis nisl ut aliquip ex ea commodo consequat. Duis autem vel eum iriure dolor in hendrerit in vulputate velit esse molestie consequat, vel illum dolore feugiat nulla facilisis at vero eros et accumsan et iusto odio dignissim qui blandit praesent luptatum zzril facilisi.</p>
  <div class="abs photo" role="img" aria-label="Support agent with a headset at an office desk with computer monitors"></div>
  <p class="abs side-text">Lorem ipsum dolor sit amet, consectetuer adipiscing elit, sed diam nonummy nibh euismod tincidunt ut laoreet dolore magna aliquam erat volutpat. Ut wisi enim ad minim veniam, quis nostrud exerci tation ullamcorper suscipit lobortis nisl ut aliquip ex ea commodo consequat. Duis autem vel eum iriure dolor in hendrerit in vulputate velit esse molestie consequat, vel illum dolore feugiat nulla facilisis at vero eros et accumsan et iusto odio dignissim qui blandit praesent luptatum zzril facilisi. Lorem ipsum dolor sit amet, consectetuer adipiscing elit, sed diam nonummy nibh euismod tincidunt ut laoreet dolore magna aliquam erat volutpat.</p>
</main>

<footer>
  <div class="abs footer"></div>
  <h3 class="footer-title" style="left:114px;top:878px">Quick Links</h3>
  <div class="footer-underline" style="left:115px;top:910px;width:114px"></div>
  <h3 class="footer-title" style="left:287px;top:878px">Contact Details</h3>
  <div class="footer-underline" style="left:288px;top:910px;width:174px"></div>
  <h3 class="footer-title" style="left:532px;top:878px">Quick Inquiry</h3>
  <div class="footer-underline" style="left:530px;top:910px;width:206px"></div>
  <div class="footer-rule" style="left:259px"></div>
  <div class="footer-rule" style="left:504px"></div>
  <div class="footer-rule" style="left:768px"></div>

  <ul class="abs quick">
    <li class="current">Home</li><li>About Us</li><li>Services</li><li>Support</li><li>Contact Us</li>
  </ul>

  <div class="abs contact">
    <div class="contact-row" style="top:0">
      <svg width="12" height="16" viewBox="0 0 12 16"><path d="M6 0a6 6 0 0 0-6 6c0 4 6 10 6 10s6-6 6-10a6 6 0 0 0-6-6zm0 8.5A2.5 2.5 0 1 1 6 3.5a2.5 2.5 0 0 1 0 5z" fill="#fff"/></svg>
      <div><b>Brimlow OrthoLink IT Inc.</b><span class="contact-address">2150 Harbor Crest Blvd – STE 410<br>Lakemont, MN 55871</span></div>
    </div>
    <div class="contact-row" style="top:90px">
      <svg width="12" height="15" viewBox="0 0 12 15"><path d="M2 0l3 4-1.6 1.6c.7 2 2 3.5 4 4.4L9 8.5l3 3-1.5 3C5 14 .5 8 0 2z" fill="#fff"/></svg>
      <b style="font-size:15px">555.014.2290</b>
    </div>
    <div class="contact-row" style="top:143px">
      <svg width="17" height="12" viewBox="0 0 17 12"><rect x=".5" y=".5" width="16" height="11" fill="none" stroke="#fff"/><path d="M.5.5l8 6 8-6" fill="none" stroke="#fff"/></svg>
      <span>hello@brimlowortholink.com</span>
    </div>
  </div>

  <form class="abs form">
    <div class="field">Name</div>
    <div class="field">Email</div>
    <div class="field">Phone</div>
    <div class="field field-message">Message</div>
    <div class="submit">SUBMIT</div>
  </form>

  <div class="abs foot-brand">Brimlow<br>OrthoLink<br>IT Inc.</div>
  <div class="abs social footer-social" aria-label="Social links"><span></span><span></span><span></span></div>

  <div class="abs copy">copyright © 2016 Brimlow OrthoLink IT Inc.&nbsp; ALL RIGHT RESERVED</div>
</footer>

</body>
</html>
```